Business Card- Can you make it cool vs boring!

Need a refresh on my business card! Want it to be modern but simple, classic and a pop of coolness! we do senior living and it is boring. but that doesn't mean our business card have to look boring! Open to two sided cards. our website is www.Dunmere-PK.com

Target Market(s)

capital market

Industry/Entity Type

senior housing/ real estate

Contact Information for Business Card

logo/ name/ cell/ address/ www.Dunmere-PK.com/ space for a QR code

Requirements
Must have
• maybe a QR code (do not make prominent I may not use the QR so design where it can be taken out) that link to more about us/ landing page. needs to be modern but clean
Should not have
• clip art or script

```html
<!DOCTYPE html>
<html lang="en">
<head>
<meta charset="utf-8">
<title>Dunmere Living — Business Card</title>
<link rel="stylesheet" href="https://fonts.googleapis.com/css2?family=Poppins:wght@400;500;600&display=swap">
<style>
  :root {
    --brand: #a84a24;
    --ink-soft: #7a7a7a;
    --card: #ffffff;
    --backdrop: #e8e3dc;
    --rule: #c9c9c9;
  }
  * { margin: 0; padding: 0; box-sizing: border-box; }
  html, body {
    width: 1189px;
    height: 1200px;
    overflow: hidden;
    background: var(--backdrop);
    font-family: "Poppins", sans-serif;
  }
  .card {
    position: absolute;
    left: 169px;
    width: 851px;
    height: 485px;
    background: var(--card);
    border-radius: 34px;
    box-shadow: 0 6px 18px rgba(0,0,0,0.12);
  }
  .card--front { top: 112px; }
  .card--back  { top: 641px; }

  .wordmark {
    position: absolute;
    color: var(--brand);
    font-weight: 500;
    white-space: nowrap;
    transform: translate(-50%, -50%);
  }
  .card--front .wordmark { left: 215px; top: 253px; font-size: 40px; }
  .card--back .wordmark  { left: 50%; top: 50%; font-size: 62px; }

  .divider {
    position: absolute;
    left: 414px;
    top: 137px;
    width: 2px;
    height: 216px;
    background: var(--rule);
  }
  .details {
    position: absolute;
    left: 454px;
    top: 128px;
    color: var(--ink-soft);
  }
  .details__name {
    color: var(--brand);
    font-weight: 600;
    font-size: 29px;
    line-height: 1.2;
  }
  .details__title {
    font-size: 17px;
    line-height: 1.2;
    margin-top: 0;
  }
  .details__address {
    font-size: 21px;
    line-height: 26px;
    margin-top: 22px;
  }
  .contact-list {
    list-style: none;
    margin-top: 12px;
  }
  .contact-list li {
    display: flex;
    align-items: center;
    gap: 12px;
    font-size: 21px;
    line-height: 28.5px;
  }
  .contact-list svg { width: 24px; height: 24px; flex: none; }
</style>
</head>
<body>
  <section class="card card--front">
    <div class="wordmark">Dunmere Living</div>
    <div class="divider"></div>
    <div class="details">
      <div class="details__name">Marcus L Reed</div>
      <div class="details__title">CEO</div>
      <div class="details__address">4870 Elmfield Avenue<br>Suite #1204</div>
      <ul class="contact-list">
        <li>
          <svg viewBox="0 0 24 24" aria-hidden="true">
            <circle cx="12" cy="12" r="12" fill="var(--brand)"/>
            <path d="M8.6 6.4 10.3 6l1 2.6-1.2 1c.6 1.5 1.6 2.6 3 3.3l1-1.2 2.6 1-.4 1.8c-.1.4-.5.7-1 .7-4-.3-7.3-3.6-7.6-7.6 0-.5.3-.9.9-1.2Z" fill="#fff"/>
          </svg>
          (555) 014-27380
        </li>
        <li>
          <svg viewBox="0 0 24 24" aria-hidden="true">
            <circle cx="12" cy="12" r="12" fill="var(--brand)"/>
            <rect x="6.5" y="8" width="11" height="8" rx="1" fill="none" stroke="#fff" stroke-width="1.4"/>
            <path d="M6.8 8.4 12 12.4l5.2-4M6.8 15.6l3.6-3.4M17.2 15.6l-3.6-3.4" fill="none" stroke="#fff" stroke-width="1.2"/>
          </svg>
          hello@dunmereliving.com
        </li>
        <li>
          <svg viewBox="0 0 24 24" aria-hidden="true">
            <circle cx="12" cy="12" r="12" fill="var(--brand)"/>
            <g fill="none" stroke="#fff" stroke-width="1.1">
              <circle cx="12" cy="12" r="5.6"/>
              <ellipse cx="12" cy="12" rx="2.4" ry="5.6"/>
              <path d="M6.4 12h11.2M7.2 9.2h9.6M7.2 14.8h9.6"/>
            </g>
          </svg>
          www.Dunmere-PK.com
        </li>
      </ul>
    </div>
  </section>

  <section class="card card--back">
    <div class="wordmark">Dunmere Living</div>
  </section>
</body>
</html>
```